Emerging automotive detailing business

I am starting a small automotive detailing business in hopes of becoming a well-known detailer to work on high end cars. I would like a card to reflect the high quality and time I put into my work. The name of the company is Bright Crest Detailing. I feel like it represents racecars getting off the line at the drag strip as well as an innuendo of "Up the Ladder". I do minor paint correction such as clay barring, multi-step buffing and polishing, waxing, hand washes, etc. I am always striving to learn more and improve my work. My goal is to have total customer satisfaction. This is a female run business but I do not want it to be very girly. Elegant is okay! I have pictures of my personal wrenfield attached, they do not need to be incorporated but if you can think of a cool way to use 1 or all of them, go for it!

Target Market(s)

Anyone that owns a vehicle. Preferably high end vehicles such as Valtori, Castellverde and Morvani but I will also happily work on any car, truck or suv no matter what brand.

Industry/Entity Type

Automotive

Contact Information for Business Card

Bright Crest Detailing
Mira Tolland
4175 Quenhollow Rd
Ashmere PA 17492
Cell phone- call/text- 717-555-0148
email- brightcrestdetails@maildrop-example.com
Instagram: @brightcrestdetailing
Facebook: facebook.com/brightcrestdetailing

Requirements
Must have
• Business name, my name, address, phone number. Listing that I do minor paint correction such as clay barring, multi-step buffing and polishing, waxing, hand washes, interior cleaning, and more. (This last part was in nice to haves but I have realized that I do really want it, so I moved it to must haves.) I want something that is different and eye-catching to my customers. Some people have done this very well with cards already submitted to me, but a lot have not. I didn't mess with the "look and feel bars" much because because I am pretty open to the overall design as long as it is not your basic run of the mill design.
Nice to have
• Something car related. Maybe an appointment time/date line. I do not have a logo, but if you would like to design one and incorporate it, that would be amazing!
Should not have
• Purple and Pink colors. Boring, basic, normal card.

```html
<!DOCTYPE html>
<html lang="en">
<head>
<meta charset="utf-8">
<title>Bright Crest Detailing – Business Card</title>
<link rel="stylesheet" href="https://fonts.googleapis.com/css2?family=Caladea:wght@700&family=Open+Sans:wght@600&family=Arimo:wght@400&display=swap">
<style>
  :root {
    --backdrop: #e9e7e4;
    --ink: #0b0b0b;
    --ink-soft: #2a2a2a;
    --card-black: #000000;
    --rule-light: #e8e8e8;
    --steel-light: #f4f5f6;
    --steel-mid: #c9cbce;
    --steel-dark: #9a9da1;
    --brush-line: rgba(255,255,255,0.18);
    --brush-shade: rgba(0,0,0,0.04);
  }
  * { box-sizing: border-box; margin: 0; padding: 0; }
  html, body {
    width: 1200px; height: 902px; overflow: hidden;
    background: var(--backdrop);
  }
  .canvas {
    width: 1200px; height: 902px;
    display: flex; flex-direction: column;
    align-items: center; justify-content: center; gap: 56px;
  }
  .card {
    position: relative;
    width: 620px; height: 354px;
    overflow: hidden;
    box-shadow: 0 10px 28px rgba(0,0,0,0.22);
  }
  .brushed {
    background:
      repeating-linear-gradient(0deg, var(--brush-line) 0 1px, transparent 1px 3px, var(--brush-shade) 3px 4px),
      linear-gradient(100deg, var(--steel-dark) 0%, var(--steel-light) 38%, var(--steel-mid) 62%, var(--steel-light) 80%, var(--steel-dark) 100%);
  }
  .brand-name {
    font-family: "Caladea", "Cambria", serif;
    font-weight: 700;
    color: var(--ink);
    white-space: nowrap;
    letter-spacing: 0.5px;
  }

  /* Front */
  .card-front { background: var(--card-black); }
  .front-band {
    position: absolute; left: 0; right: 0;
    top: 136px; height: 92px;
    display: flex; align-items: center; justify-content: center;
  }
  .front-rule {
    position: absolute; left: 0; right: 0; height: 2px;
    background: var(--rule-light);
  }
  .front-rule.upper { top: 126px; }
  .front-rule.lower { top: 236px; }
  .front-band .brand-name { font-size: 52px; }

  /* Back */
  .card-back .brand-name {
    position: absolute; left: 38px; top: 44px;
    font-size: 46px;
  }
  .back-rule {
    position: absolute; left: 38px; right: 44px; top: 112px;
    height: 2px; background: var(--ink);
  }
  .person-name {
    position: absolute; left: 78px; top: 134px;
    font-family: "Open Sans", "Segoe UI", sans-serif;
    font-weight: 600; font-size: 28px; color: var(--ink);
  }
  .contact-list {
    position: absolute; left: 78px; top: 182px;
    list-style: none;
    font-family: "Arimo", "Arial", sans-serif;
    font-size: 16px; color: var(--ink);
  }
  .contact-item {
    display: flex; align-items: center; gap: 12px;
    height: 27px;
  }
  .contact-icon {
    width: 15px; height: 15px; flex: none;
    background: var(--ink);
    display: flex; align-items: center; justify-content: center;
  }
  .contact-icon svg { width: 11px; height: 11px; }
  .services {
    position: absolute; left: 78px; right: 44px; top: 300px;
    font-family: "Arimo", "Arial", sans-serif;
    font-size: 12px; line-height: 16px;
    color: var(--ink-soft);
  }
</style>
</head>
<body>
<main class="canvas">

  <section class="card card-front" aria-label="Card front">
    <div class="front-rule upper"></div>
    <div class="front-band brushed">
      <span class="brand-name">Bright Crest Detailing</span>
    </div>
    <div class="front-rule lower"></div>
  </section>

  <section class="card card-back brushed" aria-label="Card back">
    <span class="brand-name">Bright Crest Detailing</span>
    <div class="back-rule"></div>
    <p class="person-name">Mira Tolland</p>
    <ul class="contact-list">
      <li class="contact-item">
        <span class="contact-icon">
          <svg viewBox="0 0 12 12" aria-hidden="true"><path d="M3 1.5h1.6l.8 2.2-1.1.8a6 6 0 0 0 2.2 2.2l.8-1.1 2.2.8V8a1.5 1.5 0 0 1-1.5 1.5A6.5 6.5 0 0 1 1.5 3 1.5 1.5 0 0 1 3 1.5z" fill="#fff"/></svg>
        </span>
        <span>717-555-0148</span>
      </li>
      <li class="contact-item">
        <span class="contact-icon"></span>
        <span>@brightcrestdetailing</span>
      </li>
      <li class="contact-item">
        <span class="contact-icon">
          <svg viewBox="0 0 12 12" aria-hidden="true"><rect x="1.5" y="3" width="9" height="6.5" fill="none" stroke="#fff" stroke-width="1.2"/><path d="M1.5 3l4.5 3.5L10.5 3" fill="none" stroke="#fff" stroke-width="1.2"/></svg>
        </span>
        <span>brightcrestdetails@maildrop-example.com</span>
      </li>
      <li class="contact-item">
        <span class="contact-icon">
          <svg viewBox="0 0 12 12" aria-hidden="true"><path d="M6 1a3.3 3.3 0 0 1 3.3 3.3C9.3 7 6 11 6 11S2.7 7 2.7 4.3A3.3 3.3 0 0 1 6 1z" fill="#fff"/><circle cx="6" cy="4.3" r="1.2" fill="#000"/></svg>
        </span>
        <span>4175 Quenhollow Rd, Ashmere PA 17492</span>
      </li>
    </ul>
    <p class="services">Minor paint correction: clay barring · multi-step buffing &amp; polishing · waxing · hand washes · interior cleaning &amp; more</p>
  </section>

</main>
</body>
</html>
```